Flu Vaccination Poster

I would like a banner designed to display from the ceiling in my pharmacy promoting flu vaccination.
In large words, it should say "Flu Vaccination"
In smaller text it should say "Available here. See in store for details"
It should also display our website kestrelvalepharmacy.com.au and have a message for more information visit the website.
Currently patients required to pay for the service, however in May this year the vaccine will become free for everyone, so I would like to put a sticker on the sign in May saying "FREE" and then remove the sticker when no longer free. The banner dimensions are "2.19m wide x 0.61m tall.
I have uploaded logo files plus a photo of a previously used banner which is no longer relevant. More formats of logo files are available if required.

```html
<!DOCTYPE html>
<html lang="en">
<head>
<meta charset="utf-8">
<title>Flu Vaccination Banner</title>
<link href="https://fonts.googleapis.com/css2?family=Anton&family=Montserrat:wght@400;600;700;900&display=swap" rel="stylesheet">
<style>
  :root {
    --navy: #233c66;
    --blue: #1d56a0;
    --sky: #a8d3ef;
    --pink: #d81b60;
    --white: #ffffff;
    --backdrop: #dcdcdc;
  }
  html, body {
    margin: 0;
    width: 1200px;
    height: 754px;
    overflow: hidden;
    background: var(--backdrop);
  }
  .banner {
    position: absolute;
    left: 99px;
    width: 1001px;
    height: 280px;
    display: block;
    overflow: hidden;
  }
  .banner--with-logo { top: 63px; }
  .banner--plain { top: 397px; }
  .headline, .subline, .band-text, .brand-name {
    font-family: "Montserrat", sans-serif;
  }
  .headline { fill: var(--navy); font-size: 107px; }
  .headline .heavy { font-weight: 900; }
  .headline .light { font-weight: 400; }
  .subline { fill: var(--blue); font-size: 47px; font-weight: 400; letter-spacing: -1px; }
  .subline .bold { font-weight: 700; }
  .band-text { fill: var(--sky); font-size: 25px; font-weight: 700; letter-spacing: -0.6px; }
  .brand-name { fill: var(--white); font-size: 19px; font-weight: 600; }
  .free-sticker text {
    font-family: "Anton", sans-serif;
    fill: var(--white);
    font-size: 50px;
  }
</style>
</head>
<body>

<svg class="banner banner--with-logo" viewBox="0 0 1001 280" aria-label="Flu vaccination banner with pharmacy name">
  <rect class="panel" width="1001" height="280" fill="var(--white)"/>
  <rect class="info-band" y="208" width="1001" height="72" fill="var(--navy)"/>
  <text class="headline" x="40" y="127" textLength="918" lengthAdjust="spacingAndGlyphs"><tspan class="heavy">FLU</tspan> <tspan class="light">VACCINATION</tspan></text>
  <text class="subline" x="148" y="178" textLength="705" lengthAdjust="spacingAndGlyphs">Available here. <tspan class="bold">See in store</tspan> for details</text>
  <text class="brand-name" x="25" y="237" textLength="130" lengthAdjust="spacingAndGlyphs">kestrelvale</text>
  <text class="brand-name" x="36" y="259" textLength="106" lengthAdjust="spacingAndGlyphs">pharmacy</text>
  <text class="band-text" x="187" y="253" textLength="192" lengthAdjust="spacingAndGlyphs">For More Details</text>
  <circle cx="395" cy="245" r="3.5" fill="var(--pink)"/>
  <text class="band-text" x="409" y="253" textLength="451" lengthAdjust="spacingAndGlyphs">www.kestrelvalepharmacy.com.au</text>
  <g class="free-sticker" transform="translate(924 211)">
    <circle r="52" fill="var(--pink)"/>
    <text x="-42" y="18" textLength="84" lengthAdjust="spacingAndGlyphs" transform="rotate(-8)">FREE</text>
  </g>
</svg>

<svg class="banner banner--plain" viewBox="0 0 1001 280" aria-label="Flu vaccination banner">
  <rect class="panel" width="1001" height="280" fill="var(--white)"/>
  <rect class="info-band" y="208" width="1001" height="72" fill="var(--navy)"/>
  <text class="headline" x="40" y="127" textLength="918" lengthAdjust="spacingAndGlyphs"><tspan class="heavy">FLU</tspan> <tspan class="light">VACCINATION</tspan></text>
  <text class="subline" x="148" y="178" textLength="705" lengthAdjust="spacingAndGlyphs">Available here. <tspan class="bold">See in store</tspan> for details</text>
  <text class="band-text" x="192" y="253" textLength="192" lengthAdjust="spacingAndGlyphs">For More Details</text>
  <circle cx="401" cy="245" r="3.5" fill="var(--pink)"/>
  <text class="band-text" x="413" y="253" textLength="452" lengthAdjust="spacingAndGlyphs">www.kestrelvalepharmacy.com.au</text>
  <g class="free-sticker" transform="translate(82 211)">
    <circle r="55" fill="var(--pink)"/>
    <text x="-44" y="19" textLength="88" lengthAdjust="spacingAndGlyphs">FREE</text>
  </g>
</svg>

</body>
</html>
```